International Film making Business needs the 5 Logos provided made into a POSTER Format

Design Task:
CREATE A POSTER DESIGN USING THE 5 LOGOS PROVIDED. The BOLD BRIGHT HORIZON LOGO should stand out from the others by being in the middle with the other 4 logos connected to it somehow.

The 5 Businesses already has their 5 Logos, all similar in design to each other.

BOLD BRIGHT HORIZON is the Main Logo that encompasses the other 4 Logos. So it must stand out more and it is like the Overall Business entity that incorporates the other 4 Logos.

What is required is that by using the 5 Logo designs provided, create a cool graphic artwork that somehow incorporates ALL of the 5 Logos - But having the BOLD BRIGHT HORIZON Logo at the forefront/most important/standing out the most.
- BOLD BRIGHT HORIZON will probably be bigger than the others
- and could be changed into 3D.

I have attached all 5 logos and a hand drawn example of how the BOLD BRIGHT HORIZONS could stand out from the rest.

THE DESIGNS OF THE LOGOS SHOULD NOT BE CHANGED (except the BOLDBRIGHTHORIZON which can be 3D)

Please do not be restricted with the sample idea. Creativity is encouraged

DIMENSION: 3000 mm x 6000 mm
high resolution graphic

Logo Text

bold bright , bold bright pictures, bold bright legends, bold bright groovy, BOLD BRIGHT HORIZONS

Requirements
Must have
• USE THE 5 LOGOS PROVIDED ONLY - Only BOLD BRIGHT HORIZON can be changed into 3D only
Nice to have
• Eye catching design, showing the Bold Bright Horizon as the most powerful Logo that has the other 4 as subordinate companies
Should not have
• ANY CHANGE IN THE 5 LOGO DESIGNS (EXcept 3D for Bold Bright Horizons)

```html
<!DOCTYPE html>
<html lang="en">
<head>
<meta charset="utf-8">
<title>Bold Bright Horizons – Group Poster</title>
<link rel="stylesheet" href="https://fonts.googleapis.com/css2?family=Cinzel:wght@600&family=Quicksand:wght@400&display=swap">
<style>
  :root {
    --backdrop: #4a4a4a;
    --paper: #f3e6c8;
    --panel: #f7efe1;
    --brown-top: #b9761c;
    --brown-mid: #8a3f0e;
    --brown-bottom: #561006;
    --ink-blue: #1f7fcf;
    --ink-legends: #8a2cb8;
    --ink-gold: #b68d2c;
    --ink-grey: #8d8d8d;
    --ink-black: #1b1b1b;
    --ink-green: #2a9a1e;
  }
  * { box-sizing: border-box; margin: 0; padding: 0; }
  html, body {
    width: 682px; height: 1200px; overflow: hidden;
    background: var(--backdrop);
  }
  .poster {
    position: absolute; left: 41px; top: 0;
    width: 600px; height: 1200px;
    background: var(--paper);
  }
  .poster__field {
    position: absolute; left: 18px; top: 18px; right: 18px; bottom: 18px;
    border-radius: 6px;
    background: linear-gradient(180deg, var(--brown-top) 0%, #a65e14 35%, var(--brown-mid) 62%, var(--brown-bottom) 100%);
    box-shadow: inset 0 0 18px 6px rgba(243,230,200,0.55);
  }
  .poster__connectors {
    position: absolute; left: 0; top: 0; width: 600px; height: 1200px;
  }
  .panel {
    position: absolute;
    background: var(--panel);
    border-radius: 3px;
    display: flex; align-items: center; justify-content: center;
  }
  .mark {
    flex: none; border-radius: 50%;
  }
  .wordmark {
    font-family: "Cinzel", "Times New Roman", serif;
    font-weight: 600;
    line-height: 1.02;
    letter-spacing: 0.02em;
  }
  .wordmark span { display: block; }

  .panel--bright { left: 168px; top: 86px; width: 261px; height: 127px; gap: 14px; }
  .panel--bright .mark { width: 64px; height: 64px; background: var(--ink-blue); opacity: .85; }
  .panel--bright .wordmark { color: var(--ink-blue); font-size: 25px; }

  .panel--legends { left: 110px; top: 254px; width: 376px; height: 143px; gap: 18px; }
  .panel--legends .mark { width: 86px; height: 86px; background: var(--ink-legends); opacity: .85; }
  .panel--legends .wordmark { color: var(--ink-legends); font-size: 25px; }
  .panel--legends .wordmark .line-lead { font-size: 33px; }

  .panel--horizons { left: 59px; top: 444px; width: 485px; height: 185px; gap: 20px; }
  .panel--horizons .mark { width: 132px; height: 132px; background: var(--ink-gold); opacity: .9; }
  .panel--horizons .wordmark { color: var(--ink-gold); font-size: 31px; }
  .panel--horizons .wordmark .line-lead { font-size: 40px; }
  .panel--horizons .site {
    display: block; margin-top: 6px;
    font-family: "Quicksand", "Helvetica", sans-serif;
    font-size: 13px; letter-spacing: 0.12em;
    color: var(--ink-grey);
  }

  .panel--pictures { left: 112px; top: 696px; width: 376px; height: 143px; gap: 18px; }
  .panel--pictures .mark { width: 86px; height: 86px; background: var(--ink-black); opacity: .8; }
  .panel--pictures .wordmark { color: var(--ink-black); font-size: 24px; }
  .panel--pictures .wordmark .line-lead { font-size: 34px; }

  .panel--groovy { left: 168px; top: 900px; width: 263px; height: 209px; flex-direction: column; gap: 14px; }
  .panel--groovy .mark { width: 78px; height: 78px; background: var(--ink-green); opacity: .85; }
  .panel--groovy .wordmark { color: var(--ink-green); font-size: 24px; text-align: center; }
  .panel--groovy .wordmark .line-lead { font-size: 34px; }
</style>
</head>
<body>
  <main class="poster">
    <div class="poster__field"></div>

    <svg class="poster__connectors" viewBox="0 0 1080 2160" aria-hidden="true">
      <g stroke="#f3e6c8" stroke-width="5" fill="none">
        <line x1="303" y1="383" x2="213" y2="458"/>
        <line x1="773" y1="383" x2="860" y2="458"/>
        <line x1="198" y1="715" x2="121" y2="800"/>
        <line x1="875" y1="715" x2="966" y2="800"/>
        <line x1="121" y1="1133" x2="205" y2="1253"/>
        <line x1="966" y1="1133" x2="873" y2="1253"/>
        <line x1="213" y1="1511" x2="303" y2="1620"/>
        <line x1="863" y1="1511" x2="776" y2="1620"/>
      </g>
    </svg>

    <section class="panel panel--bright">
      <div class="mark"></div>
      <h2 class="wordmark"><span>BOLD</span><span>BRIGHT</span></h2>
    </section>

    <section class="panel panel--legends">
      <div class="mark"></div>
      <h2 class="wordmark"><span>BOLD BRIGHT</span><span class="line-lead">LEGENDS</span></h2>
    </section>

    <section class="panel panel--horizons">
      <div class="mark"></div>
      <h1 class="wordmark"><span>BOLD BRIGHT</span><span class="line-lead">HORIZONS</span><span class="site">boldbrighthorizons.com.au</span></h1>
    </section>

    <section class="panel panel--pictures">
      <div class="mark"></div>
      <h2 class="wordmark"><span>BOLD BRIGHT</span><span class="line-lead">PICTURES</span></h2>
    </section>

    <section class="panel panel--groovy">
      <div class="mark"></div>
      <h2 class="wordmark"><span>BOLD BRIGHT</span><span class="line-lead">GROOVY</span></h2>
    </section>
  </main>
</body>
</html>
```